Road Construction Company needs business cards

We would like a new business card designed for our business.

We're a road construction company based in Qld, Australia.

Can the business card please have the following information on it.

Name: Warren Halbeck
Position: General Manager
Phone: 0472 915 348
Email: Warren.halbeck@tovrin.com.au
Address: 87 Marrow Ave, Pendlebay, QLD, 4023
Website: www.tovrin.com.au

Visually we'd like the card to be professional and simple.

Attached is our logo.

Our website is www.tovrin.com.au

Target Market(s)

Men aged 25-60

Contact Information for Business Card

As listed in project description

Font styles to use
Serif

Requirements
Must have
• Large logo on back of card

```html
<!DOCTYPE html>
<html lang="en">
<head>
<meta charset="utf-8">
<title>Tovrin Business Card</title>
<link href="https://fonts.googleapis.com/css2?family=Open+Sans:wght@400;600;800&display=swap" rel="stylesheet">
<style>
  :root {
    --page: #e6e6e8;
    --card-dark: #222227;
    --card-blue: #1456a6;
    --brand-blue: #1a5cb0;
    --accent: #3b9bd8;
    --band: #2f88cf;
    --text-light: #ffffff;
    --divider: #8a8a92;
    --mark-dark: #0c0c10;
  }
  * { box-sizing: border-box; margin: 0; padding: 0; }
  html, body {
    width: 1200px; height: 780px; overflow: hidden;
    background: var(--page);
    font-family: "Open Sans", Arial, sans-serif;
  }
  .sheet {
    width: 1200px; height: 780px;
    display: flex; align-items: center; justify-content: center; gap: 50px;
  }
  .card {
    position: relative;
    width: 540px; height: 310px;
    overflow: hidden;
    box-shadow: 0 6px 18px rgba(0,0,0,0.25);
  }
  .card-front { background: var(--card-dark); }
  .card-back  { background: var(--card-blue); display: flex; align-items: center; justify-content: center; }

  .front-brand {
    position: absolute; left: 30px; top: 108px;
    width: 215px;
    font-size: 48px; font-weight: 800; line-height: 1;
    color: var(--brand-blue); letter-spacing: 1px;
    white-space: nowrap;
  }
  .front-divider {
    position: absolute; left: 262px; top: 62px;
    width: 1px; height: 150px; background: var(--divider);
  }
  .contact {
    position: absolute; left: 282px; top: 66px; right: 12px;
    color: var(--text-light);
  }
  .contact-name {
    font-size: 29px; font-weight: 600; color: var(--accent); line-height: 1.1;
    white-space: nowrap;
  }
  .contact-role { font-size: 14px; margin-top: 2px; margin-bottom: 14px; }
  .contact-row {
    display: flex; align-items: center; gap: 8px;
    font-size: 13.5px; line-height: 20px; white-space: nowrap;
  }
  .contact-row svg { width: 12px; height: 12px; flex: none; fill: var(--accent); }

  .address-band {
    position: absolute; left: 0; right: 0; bottom: 26px; height: 32px;
    background: var(--band);
    color: var(--text-light); font-size: 15px;
    display: flex; align-items: center; padding-left: 26px;
  }

  .back-brand {
    font-size: 96px; font-weight: 800; line-height: 1;
    color: var(--mark-dark); letter-spacing: 3px;
  }
</style>
</head>
<body>
<main class="sheet">
  <section class="card card-front" aria-label="Business card front">
    <div class="front-brand">TOVRIN</div>
    <div class="front-divider"></div>
    <div class="contact">
      <div class="contact-name">Warren Halbeck</div>
      <div class="contact-role">General Manager</div>
      <div class="contact-row">
        <svg viewBox="0 0 24 24" aria-hidden="true"><path d="M6.6 10.8a15.1 15.1 0 0 0 6.6 6.6l2.2-2.2a1 1 0 0 1 1-.25 11.4 11.4 0 0 0 3.6.57 1 1 0 0 1 1 1V20a1 1 0 0 1-1 1A17 17 0 0 1 3 4a1 1 0 0 1 1-1h3.5a1 1 0 0 1 1 1c0 1.25.2 2.450.57 3.57a1 1 0 0 1-.25 1z"/></svg>
        <span>0472 915 348</span>
      </div>
      <div class="contact-row">
        <svg viewBox="0 0 24 24" aria-hidden="true"><path d="M12 2a10 10 0 1 0 0 20 10 10 0 0 0 0-20zm6.9 6h-2.9a15.7 15.7 0 0 0-1.4-3.6A8 8 0 0 1 18.9 8zM12 4c.8 1.2 1.5 2.5 1.9 4h-3.8c.4-1.5 1.1-2.8 1.9-4zM4.3 14a8 8 0 0 1 0-4h3.4a16 16 0 0 0 0 4zm.8 2h2.9c.3 1.3.8 2.5 1.4 3.6A8 8 0 0 1 5.1 16zM8 8H5.1a8 8 0 0 1 4.3-3.6C8.8 5.5 8.3 6.7 8 8zm4 12c-.8-1.2-1.5-2.5-1.9-4h3.8c-.4 1.5-1.1 2.8-1.9 4zm2.3-6H9.7a14.7 14.7 0 0 1 0-4h4.6a14.7 14.7 0 0 1 0 4zm.3 5.6c.6-1.1 1.1-2.3 1.4-3.6h2.9a8 8 0 0 1-4.3 3.6zm1.7-5.6a16 16 0 0 0 0-4h3.4a8 8 0 0 1 0 4z"/></svg>
        <span>www.tovrin.com.au</span>
      </div>
      <div class="contact-row">
        <svg viewBox="0 0 24 24" aria-hidden="true"><path d="M2 5h20v14H2zm2 2v.5l8 5 8-5V7zm0 2.8V17h16V9.8l-8 5z"/></svg>
        <span>Warren.halbeck@tovrin.com.au</span>
      </div>
    </div>
    <div class="address-band">87 Marrow Ave, Pendlebay, QLD, 4023</div>
  </section>

  <section class="card card-back" aria-label="Business card back">
    <div class="back-brand">TOVRIN</div>
  </section>
</main>
</body>
</html>
```